Website Design - TallyPorchHelpers.net

PLEASE CHECK WORD DOCUMENT ATTACHED FOR WEBSITE FLOW.

Target Market(s)

REAL ESTATE AGENTS ARE THE TARGET MARKET

Industry/Entity Type

Real Estate

Coding

Coded - Design and coding required

Number of Pages Required

4 page

Colors

Designer to choose colors to be used in the design.

Requirements
Must have
• WE LIKE RED LOGO ATTACHED
Nice to have
• PLEASE CHECK WORD DOCUMENT ATTACHED FOR WEBSITE FLOW.
Should not have

```html
<!DOCTYPE html>
<html lang="en">
<head>
<meta charset="utf-8">
<title>TallyPorchHelpers.net</title>
<link href="https://fonts.googleapis.com/css2?family=Mulish:wght@400;600;700;800&family=Open+Sans:wght@400;600&display=swap" rel="stylesheet">
<style>
:root{
  --navy:#231c7f;
  --navy-deep:#1a1466;
  --violet:#4a3f9e;
  --orange:#f7880f;
  --grey-bg:#e6e6e6;
  --ink:#444;
  --white:#fff;
}
*{box-sizing:border-box;margin:0;padding:0}
html,body{width:676px;height:1200px;overflow:hidden;background:var(--white)}
body{position:relative;font-family:"Open Sans",Arial,sans-serif;color:var(--ink)}
.abs{position:absolute}
.brand{font-family:"Mulish",Arial,sans-serif;font-weight:800;color:var(--navy);font-size:12px;line-height:12px;letter-spacing:.3px}
.site-header{left:0;top:0;width:676px;height:44px;background:var(--white)}
.site-header .brand{left:103px;top:11px;display:flex;align-items:center;gap:6px}
.brand-mark{width:18px;height:18px;border:2.5px solid var(--navy);border-radius:2px}
.main-nav{left:234px;top:17px;display:flex;gap:14px;font-family:"Mulish",Arial,sans-serif;font-size:8px;color:#333;letter-spacing:.3px}
.phone{left:500px;top:15px;font-family:"Mulish",Arial,sans-serif;font-size:9px;color:var(--navy);display:flex;align-items:center;gap:3px}
.hero{left:0;top:44px;width:676px;height:352px;background:linear-gradient(100deg,#5d6660 0%,#8b8f86 30%,#6c6e66 55%,#7e2a2a 75%,#9a1d1d 88%,#4b4f45 100%)}
.hero-shade{left:0;top:44px;width:676px;height:352px;background:rgba(20,20,30,.35)}
.hero-copy{left:0;top:143px;width:676px;text-align:center;color:var(--white);font-family:"Mulish",Arial,sans-serif;text-transform:uppercase}
.hero-copy h1{font-size:19px;font-weight:600;letter-spacing:.3px}
.hero-copy p{font-size:14px;font-weight:600;line-height:20px;margin-top:2px}
.slider-dots{left:319px;top:324px;display:flex;gap:3px}
.slider-dots span{width:5px;height:5px;border-radius:50%;background:var(--white)}
.slider-dots span:first-child{background:none;border:1px solid var(--white)}
.chooser h2{position:absolute;left:0;top:408px;width:676px;text-align:center;font-family:"Mulish",Arial,sans-serif;font-weight:600;font-size:15px;line-height:18px;color:var(--navy)}
.choice{position:absolute;top:461px;width:138px;height:25px;color:var(--white);font-family:"Mulish",Arial,sans-serif;font-size:7px;font-weight:600;display:flex;align-items:center;justify-content:center;letter-spacing:.2px}
.packages-bg{left:0;top:515px;width:676px;height:293px;background:var(--grey-bg)}
.packages-title{left:0;top:581px;width:676px;text-align:center;font-family:"Mulish",Arial,sans-serif;font-weight:600;font-size:13px;color:#555;letter-spacing:.3px}
.card{position:absolute;top:611px;width:90px;height:155px;background:var(--white);box-shadow:0 0 2px rgba(0,0,0,.25);text-align:center}
.card-head{height:27px;background:var(--navy);color:var(--white);font-family:"Mulish",Arial,sans-serif;font-size:8.5px;font-weight:700;padding-top:8px;clip-path:polygon(0 0,100% 0,100% 100%,50% 80%,0 100%)}
.card ul{list-style:none;font-size:6px;line-height:8.5px;color:#444;padding:6px 8px 0}
.card li{margin-bottom:6px}
.buy{display:block;margin:4px auto 0;width:60px;height:13px;background:var(--orange);color:var(--white);font-size:5px;font-weight:600;line-height:13px}
.services-bg{left:0;top:808px;width:676px;height:318px;background:linear-gradient(180deg,#2b2290 0%,#241c80 60%,#1f1870 100%)}
.services-title{left:0;top:848px;width:676px;text-align:center;color:var(--white);font-family:"Mulish",Arial,sans-serif;font-size:13px;line-height:17px;font-weight:600}
.service{position:absolute;top:923px;width:113px;height:107px;border:1px solid rgba(255,255,255,.75);text-align:center;color:var(--white)}
.service .badge{position:absolute;left:36px;top:-20px;width:40px;height:40px;border-radius:50%;background:var(--navy);border:1.5px solid var(--white);display:flex;align-items:center;justify-content:center}
.service h3{margin-top:30px;font-family:"Mulish",Arial,sans-serif;font-size:9px;font-weight:700}
.service p{font-size:6px;line-height:8.5px;padding:3px 7px 0}
.signup{left:143px;top:1051px;width:388px;height:27px;background:var(--white);border-radius:14px;display:flex;align-items:center;padding-left:16px;font-size:7.5px;color:#888;gap:5px}
.signup-btn{position:absolute;right:3px;top:3px;width:58px;height:21px;border-radius:11px;background:var(--orange);color:var(--white);font-family:"Mulish",Arial,sans-serif;font-size:8px;font-weight:600;display:flex;align-items:center;justify-content:center}
.site-footer .brand{left:107px;top:1154px;color:#999;display:flex;align-items:center;gap:6px;font-size:10px;line-height:10px}
.site-footer .brand-mark{border-color:#999;width:16px;height:16px}
.footer-nav{left:227px;top:1148px;display:flex;gap:13px;font-family:"Mulish",Arial,sans-serif;font-size:7.5px;color:#444}
.copyright{left:227px;top:1165px;font-size:5.5px;color:#666}
.social{left:493px;top:1147px;display:flex;gap:13px}
.social span{width:10px;height:10px;border-radius:50%;background:#666}
</style>
</head>
<body>
<header class="site-header abs">
  <div class="brand abs"><span class="brand-mark"></span><span>TALLY PORCH<br>HELPERS</span></div>
  <nav class="main-nav abs"><span>HOW IT WORKS</span><span>SERVICE</span><span>PRICING</span><span>ABOUT US</span><span>FAQ</span></nav>
  <div class="phone abs">
    <svg width="9" height="9" viewBox="0 0 24 24"><path fill="#231c7f" d="M6.6 10.8a15 15 0 0 0 6.6 6.6l2.2-2.2c.3-.3.7-.4 1-.2 1.1.4 2.3.6 3.6.6.6 0 1 .4 1 1V20c0 .6-.4 1-1 1A17 17 0 0 1 3 4c0-.6.4-1 1-1h3.5c.6 0 1 .4 1 1 0 1.3.2 2.5.6 3.6.1.3 0 .7-.2 1z"/></svg>
    (123) 456-7890
  </div>
</header>

<div class="hero abs" role="img" aria-label="Photo of a suburban house with a red For Sale sign in the front yard"></div>
<div class="hero-shade abs"></div>
<div class="hero-copy abs">
  <h1>Helping agents save time and money.</h1>
  <p>We place signs and boost foot traffic to your open<br>houses using proven marketing techniques.</p>
</div>
<svg class="abs" style="left:327px;top:236px" width="20" height="12" viewBox="0 0 20 12"><path d="M2 2l8 8 8-8" fill="none" stroke="#fff" stroke-width="2"/></svg>
<div class="slider-dots abs"><span></span><span></span><span></span><span></span></div>

<svg class="abs" style="left:0;top:340px" width="676" height="60" viewBox="0 0 676 60">
  <path d="M0 50 Q340 -20 676 50 L676 60 L0 60Z" fill="#fff"/>
  <path d="M30 47 Q340 -25 676 55" fill="none" stroke="#231c7f" stroke-width="2.5"/>
</svg>

<section class="chooser">
  <svg class="abs" style="left:325px;top:377px" width="26" height="22" viewBox="0 0 26 22"><path d="M3 10 L13 2 L23 10 M6 8 V20 H20 V8" fill="none" stroke="#8d88c4" stroke-width="1.5"/></svg>
  <h2>CHOOSE THE OPTION BELOW THAT<br>BEST DESCRIBES YOU</h2>
  <div class="choice" style="left:128px;background:var(--orange)">I'M A FULL ON BROKERAGE</div>
  <div class="choice" style="left:270px;background:var(--violet)">I'M AN IND. BROKER WITH A TEAM</div>
  <div class="choice" style="left:412px;background:var(--navy)">I NEED SIGN PLACEMENT ASAP</div>
</section>

<div class="packages-bg abs"></div>
<svg class="abs" style="left:0;top:513px" width="676" height="48" viewBox="0 0 676 48"><path d="M0 0 Q338 60 676 0 L676 -2 L0 -2Z" fill="#fff"/><path d="M0 2 Q338 62 676 2" fill="none" stroke="#d2d2d2" stroke-width="1.5"/></svg>
<h2 class="packages-title abs">OUR PACKAGES</h2>
<section class="packages">
  <div class="card" style="left:103px"><div class="card-head">5 SIGNS</div><ul><li>Place signs strategically in best areas according to where the open house is locateda</li><li>Pick Up the signs after the open house</li><li>Store custom signs for you if needed</li></ul><span class="buy">BUY NOW</span></div>
  <div class="card" style="left:198px"><div class="card-head">10 SIGNS</div><ul><li>Place signs strategically in best areas according to where the open house is locateda</li><li>Pick Up the signs after the open house</li><li>Store custom signs for you if needed</li></ul><span class="buy">BUY NOW</span></div>
  <div class="card" style="left:292px"><div class="card-head">15 SIGNS</div><ul><li>Place signs strategically in best areas according to where the open house is locateda</li><li>Pick Up the signs after the open house</li><li>Store custom signs for you if needed</li></ul><span class="buy">BUY NOW</span></div>
  <div class="card" style="left:387px"><div class="card-head">20 SIGNS</div><ul><li>Place signs strategically in best areas according to where the open house is locateda</li><li>Pick Up the signs after the open house</li><li>Store custom signs for you if needed</li></ul><span class="buy">BUY NOW</span></div>
  <div class="card" style="left:481px"><div class="card-head">25 SIGNS</div><ul><li>Place signs strategically in best areas according to where the open house is locateda</li><li>Pick Up the signs after the open house</li><li>Store custom signs for you if needed</li></ul><span class="buy">BUY NOW</span></div>
</section>

<div class="services-bg abs" role="img" aria-label="Blue-tinted photo of open house signs on a lawn"></div>
<h2 class="services-title abs">SIGN UP FOR A SUBSCRIPTION<br>AND GET THESE MARKETING SERVICES FOR FREE</h2>
<section class="services">
  <div class="service" style="left:102px"><div class="badge"><svg width="18" height="16" viewBox="0 0 18 16"><path d="M1 1h16v10H7l-4 4v-4H1z" fill="none" stroke="#fff" stroke-width="1.2"/><circle cx="6" cy="6" r=".9" fill="#fff"/><circle cx="9" cy="6" r=".9" fill="#fff"/><circle cx="12" cy="6" r=".9" fill="#fff"/></svg></div><h3>SMS</h3><p>Send sms blast to your neigh-borhood informing them your home is for sale and if they know anyone looking to send them over</p></div>
  <div class="service" style="left:220px"><div class="badge"><svg width="18" height="14" viewBox="0 0 18 14"><rect x="1" y="1" width="16" height="12" fill="none" stroke="#fff" stroke-width="1.2"/><path d="M1 1l8 7 8-7M1 13l6-6M17 13l-6-6" fill="none" stroke="#fff" stroke-width="1.2"/></svg></div><h3>EMAIL</h3><p>Email blast "email blast to your neighborhood informing them your home is for sale and if they know anyone looking to send them over"</p></div>
  <div class="service" style="left:340px"><div class="badge"><svg width="18" height="14" viewBox="0 0 18 14"><rect x="1" y="1" width="16" height="12" rx="1" fill="none" stroke="#fff" stroke-width="1.2"/><rect x="4" y="4" width="4" height="4" fill="#fff"/><path d="M10 5h5M10 8h5M4 10.5h11" stroke="#fff"/></svg></div><h3>FB AD</h3><p>Newsfeed ads to people in your open house area</p></div>
  <div class="service" style="left:458px"><div class="badge"><svg width="20" height="14" viewBox="0 0 20 14"><path d="M1 5h3l7-4v12l-7-4H1z" fill="none" stroke="#fff" stroke-width="1.2"/><path d="M14 4l4-2M14 7h5M14 10l4 2" stroke="#fff" stroke-width="1.2"/></svg></div><h3>VB</h3><p>VB blast "email blast to your neighborhood informing them your home is for sale and if they know anyone looking to send them over"</p></div>
</section>
<form class="signup abs">
  <svg width="10" height="8" viewBox="0 0 10 8"><rect x=".5" y=".5" width="9" height="7" fill="none" stroke="#888"/><path d="M.5 .5l4.5 4 4.5-4" fill="none" stroke="#888"/></svg>
  <span>Email address</span>
  <span class="signup-btn">SIGN UP</span>
</form>

<footer class="site-footer">
  <div class="brand abs"><span class="brand-mark"></span><span>TALLY PORCH<br>HELPERS</span></div>
  <nav class="footer-nav abs"><span>HOW IT WORKS</span><span>SERVICE</span><span>PRICING</span><span>ABOUT US</span><span>FAQ</span></nav>
  <p class="copyright abs">© 2018 Company Name &nbsp;All right reserved</p>
  <div class="social abs" aria-label="Social links"><span></span><span></span><span></span><span></span></div>
</footer>
</body>
</html>
```